Wholesale in Gold Jewellery & Gold Bullion

We are an established gold jewellery and gold bullion wholesaler selling these products to international clients. We already have a name and logo of our company, hence please view attached current card design. We need a completely new design to compliment our business and industry and the final design should be new and elegant.

Contact Information for Business Card

New card details must be same as per current card. Like logo, name, tel no. & etc.

Colors

Designer to choose colors to be used in the design.

```html
<!DOCTYPE html>
<html lang="en">
<head>
<meta charset="utf-8">
<title>Raval &amp; Co – Business Card</title>
<link rel="stylesheet" href="https://fonts.googleapis.com/css2?family=Cinzel:wght@600&family=Open+Sans:wght@400;700&display=swap">
<style>
  :root {
    --backdrop: #6b4226;
    --card-light: #dcb98f;
    --card-mid: #c69d70;
    --card-dark: #a97d52;
    --ink: #111111;
  }
  html, body {
    margin: 0;
    width: 1200px;
    height: 900px;
    overflow: hidden;
    background: var(--backdrop);
  }
  .canvas {
    position: relative;
    width: 1200px;
    height: 900px;
  }
  .card {
    position: absolute;
    width: 556px;
    height: 343px;
    background: radial-gradient(ellipse at 30% 10%, var(--card-light) 0%, var(--card-mid) 55%, var(--card-dark) 100%);
    color: var(--ink);
    text-align: center;
    box-sizing: border-box;
  }
  .card--front { left: 330px; top: 90px; }
  .card--back { left: 330px; top: 470px; }

  .holder-name {
    position: absolute;
    top: 70px;
    left: 0;
    right: 0;
    margin: 0;
    font-family: "Cinzel", serif;
    font-weight: 600;
    font-size: 21px;
    letter-spacing: 1px;
    line-height: 1;
  }
  .holder-title {
    position: absolute;
    top: 93px;
    left: 0;
    right: 0;
    margin: 0;
    font-family: "Open Sans", sans-serif;
    font-size: 15px;
    line-height: 1;
  }
  .divider {
    position: absolute;
    left: 204px;
    width: 146px;
    height: 1px;
    background: var(--ink);
  }
  .divider--upper { top: 122px; }
  .divider--lower { top: 183px; }
  .address, .contacts {
    position: absolute;
    left: 0;
    right: 0;
    margin: 0;
    font-family: "Open Sans", sans-serif;
    font-style: normal;
    font-size: 16px;
    line-height: 20px;
  }
  .address { top: 131px; }
  .contacts { top: 192px; list-style: none; padding: 0; }
  .contacts b { font-weight: 700; }

  .brand-mark {
    position: absolute;
    left: 222px;
    top: 74px;
  }
  .brand-name {
    position: absolute;
    top: 210px;
    left: 0;
    right: 0;
    margin: 0;
    font-family: "Cinzel", serif;
    font-weight: 600;
    font-size: 38px;
    letter-spacing: 1px;
    line-height: 1;
  }
</style>
</head>
<body>
<main class="canvas">
  <section class="card card--front">
    <h1 class="holder-name">Arjun Mehradev</h1>
    <p class="holder-title">Director</p>
    <div class="divider divider--upper"></div>
    <address class="address">18 Kestrel Lane,<br>Singapore 208115</address>
    <div class="divider divider--lower"></div>
    <ul class="contacts">
      <li><b>P:</b> +65 6420 1100</li>
      <li><b>M:</b> +65 9312 4458</li>
      <li><b>F:</b> +65 6385 2907</li>
      <li><b>E:</b> arjun@ravalco.com</li>
    </ul>
  </section>

  <section class="card card--back">
    <svg class="brand-mark" width="112" height="112" viewBox="0 0 112 112" aria-hidden="true">
      <circle cx="56" cy="56" r="56" fill="#111111"/>
    </svg>
    <h2 class="brand-name">Raval &amp; Co</h2>
  </section>
</main>
</body>
</html>
```